Business Card Design

I am a realtor and i also flip houses. I am CEO and Founder of my business which is Voskell Group LLC which is named after my great uncle who died and i was really close to. He was a wonderful friendly man so i want my business to represent him too. My business works with a lot of different people but i want mainly something to show i am a strong confidant woman who owns there own business. I have a really fun personality so i don't want anything TOO serious or manly. I want the perfect mix. My last two business cards i created are too embarrassing to hand out because they are far too girly and i deal with a lot of millionaire clients. I live out in the Palm Springs California area. I think its very important to show i am a single mom, female with her own business at only 24. I don't want to just be a female that blends in with all of the other serious people but yet i don't want to seem immature. People are telling me to stay away from pinks and purples but i don't want blues and greens because they represent men more. But i won't say no to them if there is a happy medium.

Industry/Entity Type

Realtor

Contact Information for Business Card

Voskell Group, LLC
Corinne Tabb
27358 Halvern Ave, C2 517
Rancho Calera, QX 40418
760-419-6735
Corinnedtabb@mailvane.com

```html
<!DOCTYPE html>
<html lang="en">
<head>
<meta charset="UTF-8">
<title>Voskell Group LLC — Corinne Tabb</title>
<link rel="stylesheet" href="https://fonts.googleapis.com/css2?family=Aldrich&display=swap">
<style>
  :root {
    --blush: #f6b6a4;
    --rose-brown: #9a6a5f;
    --cocoa: #5a3632;
    --espresso: #2a1717;
    --ink: #000000;
    --company-text: #161011;
    --contact-text: #ffffff;
    --accent-pink: #f27ab9;
  }
  * { margin: 0; padding: 0; box-sizing: border-box; }
  html, body {
    width: 1200px;
    height: 702px;
    overflow: hidden;
    background: #ffffff;
  }
  .business-card {
    position: relative;
    width: 1200px;
    height: 702px;
    background: linear-gradient(90deg,
      var(--blush) 0%,
      var(--rose-brown) 20%,
      var(--cocoa) 38%,
      var(--espresso) 58%,
      #140b0b 78%,
      var(--ink) 100%);
    font-family: "Aldrich", sans-serif;
    overflow: hidden;
  }
  .company-name {
    position: absolute;
    left: 67px;
    top: 326px;
    font-size: 45px;
    line-height: 1;
    color: var(--company-text);
    letter-spacing: 1px;
    white-space: nowrap;
  }
  .divider {
    position: absolute;
    left: 589px;
    top: 230px;
    width: 10px;
    height: 318px;
    background: var(--accent-pink);
  }
  .contact-block {
    position: absolute;
    left: 649px;
    top: 214px;
    color: var(--contact-text);
  }
  .person-name {
    font-size: 54px;
    line-height: 1;
    letter-spacing: 1px;
    font-weight: 400;
    margin-bottom: 30px;
  }
  .address-line {
    font-size: 34px;
    line-height: 64px;
    letter-spacing: 0.5px;
    white-space: nowrap;
  }
  .phone-row {
    display: flex;
    align-items: center;
    gap: 20px;
    font-size: 34px;
    line-height: 64px;
    letter-spacing: 1px;
  }
  .phone-icon { width: 44px; height: 44px; flex: none; }
  .email-row {
    position: absolute;
    left: 314px;
    top: 611px;
    display: flex;
    align-items: center;
    gap: 42px;
    color: var(--contact-text);
    font-size: 34px;
    letter-spacing: 1px;
    white-space: nowrap;
  }
  .mail-icon { width: 48px; height: 36px; flex: none; }
</style>
</head>
<body>
  <main class="business-card">
    <div class="company-name">Voskell Group LLC</div>
    <div class="divider"></div>

    <section class="contact-block">
      <h1 class="person-name">Corinne Tabb</h1>
      <p class="address-line">27358 Halvern Ave</p>
      <p class="address-line">C2 517 Rancho Calera</p>
      <p class="address-line">QX 40418</p>
      <p class="phone-row">
        <svg class="phone-icon" viewBox="0 0 24 24" aria-hidden="true">
          <path fill="var(--accent-pink)" d="M6.6 10.8c1.4 2.8 3.8 5.1 6.6 6.6l2.2-2.2c.3-.3.7-.4 1-.2 1.1.4 2.3.6 3.6.6.6 0 1 .4 1 1V20c0 .6-.4 1-1 1C10.6 21 3 13.4 3 4c0-.6.4-1 1-1h3.5c.6 0 1 .4 1 1 0 1.3.2 2.5.6 3.6.1.3 0 .7-.2 1l-2.3 2.2z"/>
        </svg>
        <span class="phone-number">760-419-6735</span>
      </p>
    </section>

    <p class="email-row">
      <svg class="mail-icon" viewBox="0 0 48 36" aria-hidden="true">
        <rect x="0" y="0" width="48" height="36" fill="var(--accent-pink)"/>
        <path d="M1 1 L24 20 L47 1 M1 35 L18 16 M47 35 L30 16" fill="none" stroke="#2a1717" stroke-width="2"/>
      </svg>
      <span class="email-address">corinnedtabb@mailvane.com</span>
    </p>
  </main>
</body>
</html>
```